New Business Card Design Project

I'd like a business card design around the same modern style that I used on my website www.brovanhs.com
It's gonna be one of those round corners double-sided business cards with maybe a big logo on the front and all the info on the back of the card.

Contact Information for Business Card

Marco Delgado
425-317-6084
www.brovanhs.com

www.facebook.com/BrovanHomeServices
www.intsgram.com/BrovanHomeServices

Requirements
Must have
• it needs to look elegant and modern

```html
<!DOCTYPE html>
<html lang="en">
<head>
<meta charset="utf-8">
<title>Brovan Home Services – Business Card</title>
<link href="https://fonts.googleapis.com/css2?family=Work+Sans:wght@400;500;700&display=swap" rel="stylesheet">
<style>
  :root {
    --bg: #1b1b1b;
    --card: #262626;
    --card-edge: #2f2f2f;
    --ink: #ffffff;
    --ink-soft: #d9d9d9;
    --accent: #1a8fd8;
    --logo: #cfcfcf;
  }
  * { margin: 0; padding: 0; box-sizing: border-box; }
  html, body {
    width: 1200px; height: 900px; overflow: hidden;
    background: var(--bg);
    font-family: "Work Sans", Arial, sans-serif;
  }
  .stage {
    width: 1200px; height: 900px;
    display: flex; flex-direction: column; align-items: center; justify-content: center;
    gap: 40px;
  }
  .card {
    width: 700px; height: 400px;
    background: linear-gradient(135deg, var(--card) 0%, var(--card-edge) 100%);
    border-radius: 18px;
    position: relative;
  }
  .card-front {
    display: flex; align-items: center; justify-content: center;
  }
  .brand-name {
    color: var(--logo);
    font-weight: 700;
    font-size: 46px;
    letter-spacing: 1px;
  }
  .card-back {
    display: flex; align-items: center; justify-content: center;
  }
  .identity {
    text-align: right;
    padding-right: 30px;
  }
  .person-name {
    color: var(--accent);
    font-size: 34px; font-weight: 500;
    letter-spacing: 2px;
    text-transform: uppercase;
  }
  .person-role {
    color: var(--ink);
    font-size: 21px;
    margin-top: 2px;
    margin-bottom: 10px;
  }
  .address {
    color: var(--ink);
    font-size: 18px; line-height: 1.4;
    font-style: normal;
    letter-spacing: 1px;
  }
  .divider {
    width: 2px; height: 120px;
    background: var(--accent);
  }
  .contacts {
    list-style: none;
    padding-left: 30px;
  }
  .contacts li {
    display: flex; align-items: center; gap: 12px;
    color: var(--ink);
    font-size: 19px; line-height: 1.4;
    letter-spacing: 1px;
  }
  .contacts svg { width: 13px; height: 13px; flex: none; }
  .contacts .mark {
    width: 11px; height: 11px; margin: 0 1px;
    background: var(--accent); border-radius: 2px; flex: none;
  }
</style>
</head>
<body>
<main class="stage">
  <section class="card card-front">
    <h1 class="brand-name">Brovan Home Services</h1>
  </section>

  <section class="card card-back">
    <div class="identity">
      <h2 class="person-name">Marco Delgado</h2>
      <p class="person-role">Director</p>
      <address class="address">2417 Harlow Creek Road<br>Oklahoma City, OK 73012</address>
    </div>
    <div class="divider"></div>
    <ul class="contacts">
      <li>
        <svg viewBox="0 0 16 16" aria-hidden="true"><path d="M4 1 L6.5 4 L5 6 Q7 10 10 11 L12 9.5 L15 12 L13 15 Q3 13 1 3 Z" fill="var(--accent)"/></svg>
        425-317-6084
      </li>
      <li>
        <svg viewBox="0 0 16 16" aria-hidden="true"><rect x="1" y="3" width="14" height="10" fill="none" stroke="var(--accent)" stroke-width="1.6"/><path d="M1 3 L8 9 L15 3" fill="none" stroke="var(--accent)" stroke-width="1.6"/></svg>
        Info@brovanhs.com
      </li>
      <li>
        <svg viewBox="0 0 16 16" aria-hidden="true"><circle cx="8" cy="8" r="6.5" fill="none" stroke="var(--accent)" stroke-width="1.4"/><ellipse cx="8" cy="8" rx="3" ry="6.5" fill="none" stroke="var(--accent)" stroke-width="1.2"/><path d="M1.5 8 H14.5" stroke="var(--accent)" stroke-width="1.2"/></svg>
        www.brovanhs.com
      </li>
      <li><span class="mark"></span>/BrovanHomeServices</li>
      <li><span class="mark"></span>/BrovanHomeServices</li>
    </ul>
  </section>
</main>
</body>
</html>
```